UI/ UX Design for ERP Software

We need a new UX/UI interface for a ERP software for property managers. Our CMMS / ERP solution is made based on responsive design technologies and is coded in PHP.
The overall UX to be similar to Tev Ulna - easy navigation, intuitive menus.

Industry/Entity Type

Property Management

Number of Pages Required

5+ page

Requirements
Must have
• Round dock buttons
Consistent icons across the application
Enough Spacing between buttons/icons/ menu
Consistent Font
Nice to have
• We would like the UX to allow the users to use the application without /minimum training.
Should not have
• we don't want anything that is classic with respect to UX

```html
<!DOCTYPE html>
<html lang="en">
<head>
<meta charset="utf-8">
<title>Estato – Maintenance calendar</title>
<link href="https://fonts.googleapis.com/css2?family=Inter:wght@500;600;700&display=swap" rel="stylesheet">
<style>
  :root{
    --page:#1b1c23;
    --app:#262730;
    --board:#30323e;
    --cell:#323543;
    --cell-past:#23242c;
    --cell-line:#596076;
    --cell-line-past:#6f93b4;
    --tab:#30323d;
    --text:#ffffff;
    --muted:#c9ccd6;
    --blue:#1479e0;
    --blue-bright:#0a93f5;
    --orange:#f0703e;
    --orange-bright:#fb7f2f;
  }
  *{box-sizing:border-box;margin:0;padding:0}
  html,body{width:1200px;height:1200px;overflow:hidden;background:var(--page);font-family:"Inter",sans-serif;color:var(--text)}
  .app{position:absolute;left:140px;top:0;width:920px;height:1200px;background:var(--app)}
  .brand{position:absolute;left:28px;top:26px;display:flex;align-items:center;gap:6px;font-size:15px;font-weight:600}
  .brand-mark{width:12px;height:12px;background:var(--text);border-radius:2px}
  .theme-toggle{position:absolute;left:658px;top:36px;width:55px;height:23px;border-radius:12px;background:#1e1f26;display:flex;align-items:center;justify-content:space-around;padding:0 4px}
  .welcome{position:absolute;right:78px;top:40px;font-size:11px;font-weight:500}
  .welcome b{font-weight:700}
  .avatar{position:absolute;left:855px;top:30px;width:35px;height:35px;border-radius:50%;background:radial-gradient(circle at 50% 40%,#8a6a55,#3b3f4c)}
  .section-title{position:absolute;left:34px;top:80px;display:flex;align-items:center;gap:10px;font-size:15.5px;font-weight:700}
  .tabs{position:absolute;left:33px;top:116px;display:flex;gap:5.5px}
  .tab{width:95px;height:29px;border-radius:4px;background:var(--tab);font-size:8px;font-weight:600;display:flex;align-items:center;justify-content:center}
  .views{position:absolute;left:33px;top:163px;display:flex;gap:11px}
  .view-btn{height:41px;border-radius:4px;display:flex;align-items:center;justify-content:center;gap:6px;font-size:10px;font-weight:600}
  .view-btn.requests{width:142px;background:#f4f6fa;color:#1f2230}
  .view-btn.calendar{width:160px;background:var(--blue-bright);box-shadow:0 4px 16px rgba(10,147,245,.35)}
  .month{position:absolute;left:640px;top:222px;width:250px;height:26px;display:flex;align-items:center;justify-content:flex-end;gap:16px}
  .month-label{font-size:16px;font-weight:700;margin-right:8px}
  .nav-btn{width:26px;height:26px;border:1px solid #d9dce4;border-radius:3px;display:flex;align-items:center;justify-content:center}
  .board{position:absolute;left:28px;top:261px;width:862px;height:822px;background:var(--board);border-radius:6px;padding:0 13px}
  .weekdays{display:grid;grid-template-columns:repeat(7,1fr);gap:5.5px;height:39px;align-items:center;text-align:center;font-size:12.5px;font-weight:600}
  .days{display:grid;grid-template-columns:repeat(7,1fr);grid-auto-rows:184px;gap:6px 5.5px}
  .day{position:relative;background:var(--cell);border:1px solid var(--cell-line)}
  .day.outside{background:var(--cell-past);border-color:var(--cell-line-past)}
  .day-num{position:absolute;right:7px;top:10px;font-size:10.5px;font-weight:700}
  .event{position:absolute;left:-1px;right:-1px;height:29px;padding:4px 8px;font-size:7.4px;font-weight:600;line-height:11px}
  .event.first{top:43px}
  .event.second{top:83px}
  .event.blue{background:var(--blue)}
  .event.orange{background:var(--orange)}
  .dock{position:absolute;left:387px;top:1113px;width:146px;height:57px;border-radius:8px;background:#1f2028;display:flex;align-items:center;justify-content:center;gap:30px}
  .dock-btn{width:39px;height:39px;border-radius:9px;display:flex;align-items:center;justify-content:center}
  .dock-btn.home{background:linear-gradient(160deg,#13b0ff,#0879ec);box-shadow:0 4px 14px rgba(10,147,245,.45)}
  .dock-btn.menu{background:linear-gradient(160deg,#ff9a3a,#f4692a);box-shadow:0 4px 14px rgba(251,127,47,.45)}
</style>
</head>
<body>
<main class="app">
  <div class="brand"><span class="brand-mark"></span>Estato</div>

  <div class="theme-toggle">
    <svg width="13" height="13" viewBox="0 0 14 14"><circle cx="7" cy="7" r="6" fill="none" stroke="#5b5f6d" stroke-width="1.5"/></svg>
    <svg width="13" height="13" viewBox="0 0 14 14"><path d="M9 1.5a5.5 5.5 0 1 0 3.5 8.5A5 5 0 0 1 9 1.5z" fill="none" stroke="#fff" stroke-width="1.3"/></svg>
  </div>
  <div class="welcome">Welcome, <b>Dana Reyes</b></div>
  <div class="avatar" role="img" aria-label="User profile photo"></div>

  <h1 class="section-title">
    <svg width="18" height="18" viewBox="0 0 18 18" fill="none" stroke="#d8dbe3" stroke-width="1.2"><rect x="2" y="2" width="9" height="14"/><rect x="11" y="7" width="5" height="9"/><path d="M4 5h5M4 8h5M4 11h5M13 10h1.5M13 12.5h1.5M6 16v-2.5h2V16"/></svg>
    Properties list
  </h1>

  <nav class="tabs">
    <div class="tab">Prime tower</div><div class="tab">Prime tower</div><div class="tab">Prime tower</div><div class="tab">Prime tower</div><div class="tab">Prime tower</div><div class="tab">Prime tower</div><div class="tab">Prime tower</div>
  </nav>

  <div class="views">
    <div class="view-btn requests">
      <svg width="12" height="13" viewBox="0 0 12 13" fill="none" stroke="#1f2230" stroke-width="1.3"><rect x="1" y="2" width="10" height="10" rx="1"/><path d="M4 1v2M8 1v2"/></svg>
      Request / orders
    </div>
    <div class="view-btn calendar">
      <svg width="12" height="12" viewBox="0 0 12 12" fill="none" stroke="#fff" stroke-width="1.2"><rect x="1" y="2" width="10" height="9" rx="1"/><path d="M1 5h10M4 1v2M8 1v2"/></svg>
      Maintenance calendar
    </div>
  </div>

  <div class="month">
    <span class="month-label">January 2021</span>
    <span class="nav-btn"><svg width="8" height="10" viewBox="0 0 8 10"><path d="M6 1L2 5l4 4" fill="none" stroke="#fff" stroke-width="1.6"/></svg></span>
    <span class="nav-btn"><svg width="8" height="10" viewBox="0 0 8 10"><path d="M2 1l4 4-4 4" fill="none" stroke="#fff" stroke-width="1.6"/></svg></span>
  </div>

  <section class="board">
    <div class="weekdays">
      <span>Sunday</span><span>Monday</span><span>Tuesday</span><span>Wednesday</span><span>Thursday</span><span>Friday</span><span>Saturday</span>
    </div>
    <div class="days">
      <div class="day outside"><span class="day-num">27</span></div>
      <div class="day outside"><span class="day-num">28</span></div>
      <div class="day outside"><span class="day-num">29</span></div>
      <div class="day outside"><span class="day-num">30</span></div>
      <div class="day outside"><span class="day-num">31</span></div>
      <div class="day"><span class="day-num">01</span><div class="event first blue">Maintenance Prime tower<br>6:00</div><div class="event second orange">Maintenance Prime tower<br>6:00</div></div>
      <div class="day"><span class="day-num">02</span></div>

      <div class="day"><span class="day-num">03</span></div>
      <div class="day"><span class="day-num">04</span></div>
      <div class="day"><span class="day-num">05</span></div>
      <div class="day"><span class="day-num">06</span></div>
      <div class="day"><span class="day-num">07</span><div class="event first blue">Maintenance Prime tower<br>6:00</div><div class="event second orange">Maintenance Prime tower<br>6:00</div></div>
      <div class="day"><span class="day-num">08</span></div>
      <div class="day"><span class="day-num">09</span></div>

      <div class="day"><span class="day-num">10</span></div>
      <div class="day"><span class="day-num">11</span><div class="event first blue">Maintenance Prime tower<br>6:00</div></div>
      <div class="day"><span class="day-num">12</span><div class="event first blue">Maintenance Prime tower<br>6:00</div></div>
      <div class="day"><span class="day-num">13</span></div>
      <div class="day"><span class="day-num">14</span><div class="event first blue">Maintenance Prime tower<br>6:00</div><div class="event second orange">Maintenance Prime tower<br>6:00</div></div>
      <div class="day"><span class="day-num">15</span></div>
      <div class="day"><span class="day-num">16</span><div class="event first blue">Maintenance Prime tower<br>6:00</div><div class="event second orange">Maintenance Prime tower<br>6:00</div></div>

      <div class="day"><span class="day-num">17</span><div class="event first blue">Maintenance Prime tower<br>6:00</div><div class="event second orange">Maintenance Prime tower<br>6:00</div></div>
      <div class="day"><span class="day-num">18</span></div>
      <div class="day"><span class="day-num">19</span><div class="event first blue">Maintenance Prime tower<br>6:00</div><div class="event second orange">Maintenance Prime tower<br>6:00</div></div>
      <div class="day"><span class="day-num">20</span></div>
      <div class="day"><span class="day-num">21</span></div>
      <div class="day"><span class="day-num">22</span><div class="event first blue">Maintenance Prime tower<br>6:00</div><div class="event second orange">Maintenance Prime tower<br>6:00</div></div>
      <div class="day"><span class="day-num">23</span></div>
    </div>
  </section>

  <nav class="dock">
    <div class="dock-btn home">
      <svg width="16" height="15" viewBox="0 0 16 15"><path d="M8 1L1.5 7H3.5V14H6.5V10H9.5V14H12.5V7H14.5Z" fill="#fff" stroke="#fff" stroke-linejoin="round"/></svg>
    </div>
    <div class="dock-btn menu">
      <svg width="16" height="16" viewBox="0 0 16 16" fill="#fff"><circle cx="3" cy="3" r="1.5"/><circle cx="8" cy="3" r="1.5"/><circle cx="13" cy="3" r="1.5"/><circle cx="3" cy="8" r="1.5"/><circle cx="8" cy="8" r="1.5"/><circle cx="13" cy="8" r="1.5"/><circle cx="3" cy="13" r="1.5"/><circle cx="8" cy="13" r="1.5"/><circle cx="13" cy="13" r="1.5"/></svg>
    </div>
  </nav>
</main>
</body>
</html>
```